Hueverberant (Synth Presets Expansion Pack)

Hello Designers! I'm an audio engineer and beat maker who is about to start selling sound packs on my website www.brindlemoorstudio.com. I'm looking to have some art created for my new QUARTZEN Preset Bank called "Hueverberant". QUARTZEN is a Synth from Pellow Acoustics if you want to learn more about it. Hueverberant is a sub type of synthesthesia, a syndrome where people see colors when they hear sounds. Check out this video to learn more https://www.vidlorn.com/watch?v=kq7TzwPmd3X
I've attached some examples of another producers sound pack graphics and boxes, so you have an idea of what I'm looking for. I also have attached two pictures of "Hueverberant" to inspire the graphics I'm hoping for on my new product. I would like my product to say "www.BrindleMoorStudio.com Presents" at the top. At the bottom I would like my logo to go on the bottom left. Please also add the Lumo and KT logo on the bottom right. If you have any questions please let me know.

Target Market(s)

97% of my customers are upcoming producers, 18-45 years old, and are guys.

Industry/Entity Type

Audio

Requirements
Must have
• What I asked for in the description.

```html
<!DOCTYPE html>
<html lang="en">
<head>
<meta charset="utf-8">
<title>Hueverberant – Preset Bank Box Front</title>
<link rel="stylesheet" href="https://fonts.googleapis.com/css2?family=Arimo:wght@400;700&display=swap">
<style>
  :root {
    --stage: #a9abae;
    --face-top: #dcdde0;
    --face-mid: #f4f4f5;
    --face-white: #ffffff;
    --ink: #1b1b1d;
    --accent-blue: #1f5fd0;
    --band-grey: #c9cbcf;
    --sky-black: #141414;
    --eq-purple: #8a3fb8;
    --eq-magenta: #d43c8f;
    --eq-yellow: #e9d24a;
    --eq-green: #4cc06a;
    --eq-cyan: #2fa6d8;
    --eq-blue: #3458c9;
    --mark-bg: #c8378a;
    --device-grey: #6b6e73;
  }
  * { box-sizing: border-box; margin: 0; padding: 0; }
  html, body { width: 1200px; height: 900px; overflow: hidden; }
  body {
    background: var(--stage);
    font-family: "Arimo", Arial, sans-serif;
    display: flex;
    align-items: center;
    justify-content: center;
  }
  .box-front {
    position: relative;
    width: 620px;
    height: 860px;
    background: linear-gradient(to bottom, var(--face-top) 0%, var(--face-mid) 16%, var(--face-white) 45%, var(--face-mid) 100%);
    overflow: hidden;
  }
  .top-band {
    position: absolute;
    inset: 0 0 auto 0;
    height: 140px;
    background: linear-gradient(to bottom, var(--band-grey), rgba(255,255,255,0));
  }
  .presenter {
    position: absolute;
    top: 36px;
    left: 0;
    right: 0;
    text-align: center;
  }
  .presenter-url {
    font-weight: 700;
    font-size: 17px;
    letter-spacing: 1.5px;
    color: var(--ink);
  }
  .presenter-label {
    margin-top: 6px;
    font-weight: 700;
    font-size: 14px;
    letter-spacing: 7px;
    color: var(--accent-blue);
  }
  .hero-art {
    position: absolute;
    top: 150px;
    left: 80px;
    width: 460px;
    height: 420px;
    border-radius: 50% 50% 30% 30%;
    background: radial-gradient(circle at 50% 55%, #f06fbf 0%, #6fd0e8 30%, #3b6fd6 55%, rgba(40,40,40,0.85) 80%, rgba(255,255,255,0) 100%);
  }
  .skyline-art {
    position: absolute;
    left: 0;
    right: 0;
    bottom: 0;
    height: 330px;
    background:
      linear-gradient(to bottom, var(--sky-black) 0%, var(--sky-black) 22%, rgba(255,255,255,0) 36%, rgba(255,255,255,0) 62%, rgba(255,255,255,0.85) 100%),
      linear-gradient(to right, var(--eq-purple), var(--eq-magenta) 25%, var(--eq-yellow) 50%, var(--eq-green) 65%, var(--eq-cyan) 80%, var(--eq-blue));
  }
  .device-art {
    position: absolute;
    left: 30px;
    bottom: 70px;
    width: 190px;
    height: 110px;
    background: linear-gradient(to bottom, #8d9095, var(--device-grey));
  }
  .brand-mark {
    position: absolute;
    left: 30px;
    bottom: 30px;
    display: flex;
    align-items: center;
    gap: 8px;
    font-weight: 700;
    font-size: 16px;
    color: var(--ink);
  }
  .brand-mark .brand-square {
    width: 18px;
    height: 18px;
    background: var(--ink);
  }
  .platforms {
    position: absolute;
    right: 30px;
    bottom: 30px;
    display: flex;
    gap: 6px;
  }
  .platform-tag {
    font-weight: 700;
    font-size: 13px;
    color: var(--face-white);
    background: var(--mark-bg);
    padding: 3px 7px;
  }
</style>
</head>
<body>
  <main class="box-front">
    <div class="top-band"></div>

    <header class="presenter">
      <p class="presenter-url">www.brindlemoorstudio.com</p>
      <p class="presenter-label">PRESENTS</p>
    </header>

    <div class="hero-art" role="img" aria-label="Illustration of two silhouetted figures jumping hand in hand inside large headphones, surrounded by colourful paint splashes and dots"></div>

    <div class="skyline-art" role="img" aria-label="Black city skyline silhouette reflected into a rainbow-coloured audio equalizer"></div>

    <div class="device-art" role="img" aria-label="Picture of a drum-pad music production controller"></div>

    <footer class="brand-mark">
      <span class="brand-square"></span>
      <span class="brand-name">BrindleMoor Studio</span>
    </footer>

    <div class="platforms">
      <span class="platform-tag">Lumo</span>
      <span class="platform-tag">KT</span>
    </div>
  </main>
</body>
</html>
```